New Business Card Design

We would like to refresh our business cards and make them look better. We are an IT company specialising in Cloud Services, IT Managed Services, software and hardware. I have attached a PSD of our current design. Also attached our logo.
Updates

I have uploaded all new logos in EPS format.

Can you please edit all designs to include a job title for Marcus Hollis, eg. General Manager

Industry/Entity Type

Software

Colors
ffffff

Requirements
Must have
• Please use white background.
Should not have
• Black background

```html
<!DOCTYPE html>
<html lang="en">
<head>
<meta charset="utf-8">
<title>Clearpath Systems – Business Cards</title>
<link href="https://fonts.googleapis.com/css2?family=Questrial&display=swap" rel="stylesheet">
<style>
  :root {
    --page: #e9e9ea;
    --card-top: #ffffff;
    --card-bottom: #e4e5e7;
    --ink: #3a3d42;
    --ink-soft: #6e737a;
    --brand-red: #c8442a;
    --brand-red-light: #e79a85;
    --dot-grey: #7d8791;
    --dot-grey-light: #9aa3ab;
  }
  * { box-sizing: border-box; margin: 0; padding: 0; }
  html, body {
    width: 1200px; height: 900px; overflow: hidden;
    background: var(--page);
    font-family: "Questrial", "Century Gothic", sans-serif;
    color: var(--ink);
  }
  .canvas { position: relative; width: 1200px; height: 900px; }

  .card {
    position: absolute; left: 320px;
    width: 560px; height: 340px;
    border-radius: 18px; overflow: hidden;
    background: linear-gradient(160deg, var(--card-top) 35%, var(--card-bottom) 100%);
    box-shadow: 0 10px 28px rgba(0,0,0,0.18);
  }
  .card--front { top: 70px; }
  .card--back { top: 490px; }

  /* dotted brand bands */
  .band-red, .band-grey { position: absolute; top: 0; height: 100%; }
  .band-red { background: linear-gradient(90deg, var(--brand-red) 0%, var(--brand-red-light) 100%); }
  .band-grey { background: linear-gradient(180deg, var(--dot-grey-light), var(--dot-grey)); }

  .card--front .band-grey { right: 152px; width: 26px; }
  .card--front .band-red { right: 0; width: 146px;
    background: linear-gradient(270deg, var(--brand-red) 0%, var(--brand-red-light) 100%); }

  .card--back .band-red { left: 0; width: 30px; }
  .card--back .band-grey { left: 36px; width: 30px; }

  /* wordmark */
  .wordmark { display: flex; align-items: center; gap: 10px; }
  .wordmark__dot { width: 26px; height: 26px; border-radius: 50%; background: var(--brand-red); }
  .wordmark__name {
    font-size: 26px; letter-spacing: 4px; color: var(--ink-soft); line-height: 1;
  }

  .card--front .wordmark { position: absolute; left: 34px; bottom: 92px; }
  .tagline {
    position: absolute; left: 70px; bottom: 56px;
    font-size: 12px; letter-spacing: 0.5px; color: var(--ink);
  }

  .card--back .wordmark { position: absolute; right: 34px; top: 36px; }

  .person { position: absolute; left: 110px; top: 140px; }
  .person__name { font-size: 34px; color: var(--ink); line-height: 1; }
  .person__title { font-size: 14px; color: var(--ink-soft); margin-left: 72px; margin-top: 2px; }

  .contact {
    position: absolute; right: 34px; top: 208px;
    list-style: none; font-size: 14px; color: var(--ink);
  }
  .contact li { display: flex; align-items: center; gap: 10px; height: 21px; }
  .contact svg { width: 11px; height: 11px; fill: var(--ink-soft); flex: none; }
</style>
</head>
<body>
<main class="canvas">

  <section class="card card--front" aria-label="Business card front">
    <div class="band-grey" role="img" aria-label="Column of grey brand dots"></div>
    <div class="band-red" role="img" aria-label="Field of red brand dots"></div>
    <div class="wordmark">
      <span class="wordmark__dot"></span>
      <span class="wordmark__name">clearpath systems</span>
    </div>
    <p class="tagline">IT SERVICES, SOLUTIONS AND SUPPORT</p>
  </section>

  <section class="card card--back" aria-label="Business card back">
    <div class="band-red" role="img" aria-label="Column of red brand dots"></div>
    <div class="band-grey" role="img" aria-label="Column of grey brand dots"></div>
    <div class="wordmark">
      <span class="wordmark__dot"></span>
      <span class="wordmark__name">clearpath systems</span>
    </div>
    <div class="person">
      <h1 class="person__name">Marcus Hollis</h1>
      <p class="person__title">general manager</p>
    </div>
    <ul class="contact">
      <li><svg viewBox="0 0 12 12"><path d="M2 1l2 0 1 3-1.5 1a6 6 0 0 0 3.5 3.5L8 7l3 1v2a1 1 0 0 1-1 1A9 9 0 0 1 1 2a1 1 0 0 1 1-1z"/></svg>07 3555 0142</li>
      <li><svg viewBox="0 0 12 12"><path d="M3 0h6a1 1 0 0 1 1 1v10a1 1 0 0 1-1 1H3a1 1 0 0 1-1-1V1a1 1 0 0 1 1-1zm0 2v7h6V2z"/></svg>0400 555 318</li>
      <li><svg viewBox="0 0 12 12"><path d="M6 1a5 5 0 1 0 3 9l-.6-.8A4 4 0 1 1 10 6v.8a1 1 0 0 1-2 0V3.5H7v.4A2.5 2.5 0 1 0 8.2 8 2 2 0 0 0 11 6.8V6a5 5 0 0 0-5-5zm0 3.5a1.5 1.5 0 1 1 0 3 1.5 1.5 0 0 1 0-3z"/></svg>mhollis@clearpathit.com.au</li>
      <li><svg viewBox="0 0 12 12"><path d="M6 1l6 5h-2v5H7.5V8h-3v3H2V6H0z"/></svg>www.clearpathit.com.au</li>
    </ul>
  </section>

</main>
</body>
</html>
```